Additional Benefits of Working for VELMAR

Please prepare an infographic on the additional benefits besides salary of working at VELMAR as detailed in the attached word document. Also attached is our logo in eps and our company design "Grounds". We are a Not For Profit company that finds jobs for unemployed people of government benefit payments

Target Market(s)

Attracting people to work for VELMAR. Making VELMAR an employer of choice.

Font styles to use
Sans Serif

Colors

Designer to choose colors to be used in the design.

Requirements
Must have
• be on 1 page
• have our logo
Nice to have
• Our Grounds design worked into it.
• Happy engaged employees
• Community engagement - we are a not for profit organisation
Should not have
• Discrimination, swearing,

```html
<!DOCTYPE html>
<html lang="en">
<head>
<meta charset="utf-8">
<title>Benefits of Working with Us – VELMAR</title>
<link href="https://fonts.googleapis.com/css2?family=Questrial&display=swap" rel="stylesheet">
<style>
  :root{
    --teal:#13866f;
    --teal-dark:#0c6f5a;
    --teal-light:#1fa384;
    --orange:#d8882b;
    --orange-light:#f5bd72;
    --orange-dark:#c26f1c;
    --gold:#f2b96c;
    --ink:#1d1d1d;
    --paper:#ffffff;
  }
  *{box-sizing:border-box;margin:0;padding:0}
  html,body{width:1200px;height:1142px;overflow:hidden;background:var(--paper)}
  body{position:relative;font-family:"Questrial",sans-serif;color:var(--ink)}

  .brand{position:absolute;left:40px;top:50px;height:86px;display:flex;align-items:center;
    font-size:84px;letter-spacing:-3px;color:var(--ink);line-height:1}

  .title-pill{position:absolute;left:365px;top:33px;width:772px;height:106px;border-radius:30px;
    background:linear-gradient(180deg,var(--teal-light),var(--teal-dark));
    box-shadow:0 6px 8px rgba(0,0,0,.25);display:flex;align-items:center;justify-content:center}
  .title-pill h1{font-weight:400;font-size:50px;color:var(--gold);letter-spacing:.5px}

  .connectors{position:absolute;inset:0;width:1200px;height:1142px}

  .icon-ring{position:absolute;width:120px;height:120px;margin:-60px 0 0 -60px;border-radius:50%;
    background:var(--paper);border:5px solid var(--teal);display:flex;align-items:center;justify-content:center}
  .icon-ring svg{width:64px;height:64px;fill:none;stroke:var(--teal);stroke-width:3;stroke-linecap:round;stroke-linejoin:round}

  .card{position:absolute;border:4px solid var(--orange);border-radius:16px;overflow:hidden;background:#d4d4d4;
    display:flex;flex-direction:column;box-shadow:0 2px 3px rgba(0,0,0,.15)}
  .card-head{background:linear-gradient(180deg,var(--orange-light),var(--orange) 70%,var(--orange-dark));
    color:var(--teal-dark);text-align:center;font-size:22px;line-height:1.2;padding:8px 6px 7px}
  .card-body{position:relative;flex:1}
  .grounds{position:absolute;inset:0;
    background:linear-gradient(135deg,#cfcfcf 0%,#b9bfb7 30%,#d9d2b6 55%,#c3c6c0 75%,#b5b8b3 100%)}
  .card-list{position:relative;list-style:none;padding:9px 11px;font-size:12.6px;line-height:1.5}
  .card-list li{margin-bottom:6px;text-align:justify}
  .card-list li::before{content:"• "}
</style>
</head>
<body>

<div class="brand">velmar</div>
<div class="title-pill"><h1>Benefits of Working with Us</h1></div>

<svg class="connectors" viewBox="0 0 1200 1142" aria-hidden="true">
  <g stroke="#13866f" stroke-width="5" fill="none">
    <line x1="154" y1="222" x2="1005" y2="222"/>
    <line x1="29" y1="442" x2="1137" y2="442"/>
    <line x1="150" y1="716" x2="1005" y2="716"/>
    <line x1="26" y1="891" x2="1137" y2="891"/>
    <line x1="1005" y1="560" x2="1005" y2="716"/>
    <line x1="154" y1="282" x2="154" y2="305"/>
    <line x1="426" y1="282" x2="426" y2="305"/>
    <line x1="719" y1="282" x2="719" y2="305"/>
    <line x1="1005" y1="282" x2="1005" y2="312"/>
    <line x1="150" y1="776" x2="150" y2="810"/>
    <line x1="426" y1="776" x2="426" y2="807"/>
    <line x1="719" y1="776" x2="719" y2="810"/>
    <line x1="1005" y1="776" x2="1005" y2="810"/>
  </g>
</svg>

<!-- icons row 1 -->
<div class="icon-ring" style="left:154px;top:222px">
  <svg viewBox="0 0 64 64"><line x1="32" y1="8" x2="32" y2="54"/><line x1="12" y1="18" x2="52" y2="18"/><circle cx="32" cy="8" r="3"/><path d="M12 18 L4 36 H20 Z"/><path d="M52 18 L44 36 H60 Z"/><line x1="20" y1="56" x2="44" y2="56"/></svg>
</div>
<div class="icon-ring" style="left:426px;top:222px">
  <svg viewBox="0 0 64 64"><path d="M32 54 L10 32 C2 24 6 10 18 10 C25 10 30 15 32 19 C34 15 39 10 46 10 C58 10 62 24 54 32 Z"/><path d="M32 46 L16 30 C11 25 13 16 20 16"/></svg>
</div>
<div class="icon-ring" style="left:719px;top:222px">
  <svg viewBox="0 0 64 64"><path d="M6 6 V58 H58"/><line x1="16" y1="56" x2="16" y2="40"/><line x1="26" y1="56" x2="26" y2="32"/><line x1="36" y1="56" x2="36" y2="38"/><line x1="46" y1="56" x2="46" y2="24"/><path d="M12 38 L24 24 L34 32 L54 10"/><path d="M44 10 H54 V20"/></svg>
</div>
<div class="icon-ring" style="left:1005px;top:222px">
  <svg viewBox="0 0 64 64"><rect x="10" y="14" width="40" height="40" rx="3"/><path d="M14 14 L40 8 L44 14"/><rect x="34" y="28" width="20" height="12" rx="2"/><circle cx="40" cy="34" r="2"/></svg>
</div>

<!-- icons row 2 -->
<div class="icon-ring" style="left:150px;top:716px">
  <svg viewBox="0 0 64 64"><circle cx="32" cy="32" r="24"/><ellipse cx="32" cy="32" rx="10" ry="24"/><line x1="8" y1="32" x2="56" y2="32"/><path d="M12 20 H52 M12 44 H52"/></svg>
</div>
<div class="icon-ring" style="left:426px;top:716px">
  <svg viewBox="0 0 64 64"><path d="M4 10 H12 L18 42 H52 L58 18 H14"/><line x1="22" y1="26" x2="56" y2="26"/><line x1="20" y1="34" x2="54" y2="34"/><line x1="30" y1="18" x2="30" y2="42"/><line x1="42" y1="18" x2="42" y2="42"/><circle cx="22" cy="52" r="4"/><circle cx="48" cy="52" r="4"/></svg>
</div>
<div class="icon-ring" style="left:719px;top:716px">
  <svg viewBox="0 0 64 64"><path d="M20 4 H44 V20 L32 28 L20 20 Z"/><circle cx="32" cy="42" r="16"/><path d="M32 33 L35 39 L41 40 L36.5 44 L38 50 L32 47 L26 50 L27.5 44 L23 40 L29 39 Z"/></svg>
</div>
<div class="icon-ring" style="left:1005px;top:716px">
  <svg viewBox="0 0 64 64"><path d="M32 50 V24"/><path d="M32 30 C24 30 14 24 12 14 C22 14 30 20 32 30"/><path d="M32 24 C34 14 44 6 56 6 C54 18 44 24 32 24"/><path d="M8 56 C14 48 24 48 32 50 C40 48 50 48 56 56 Z"/></svg>
</div>

<!-- row 1 cards -->
<section class="card" style="left:29px;top:303px;width:257px;height:333px">
  <h2 class="card-head">Life Balance</h2>
  <div class="card-body">
    <div class="grounds" role="img" aria-label="Company Grounds pattern in soft grey, sage and sand tones"></div>
    <ul class="card-list">
      <li>VELMAR Day Leave. An extra day off at Christmas</li>
      <li>BIRTHDAY Leave. A paid day off on your birthday</li>
      <li>A day off every month as Time in Lieu</li>
      <li>4 weeks Annual Leave</li>
      <li>Generous Personal Leave</li>
      <li>Support for parental leave for the birth or adoption of a child</li>
      <li>Flexible work arrangements</li>
    </ul>
  </div>
</section>

<section class="card" style="left:310px;top:303px;width:258px;height:303px">
  <h2 class="card-head">Wellbeing</h2>
  <div class="card-body">
    <div class="grounds" role="img" aria-label="Company Grounds pattern in soft grey, sage and sand tones"></div>
    <ul class="card-list">
      <li>Up to $450 per year to spend on Wellbeing services such as gym or yoga memberships</li>
      <li>Free counselling services 24x7 via our Employee Assistance Program</li>
      <li>Discount private health insurance</li>
      <li>WHS policies which support a safe, inclusive work place</li>
    </ul>
  </div>
</section>

<section class="card" style="left:593px;top:303px;width:258px;height:330px">
  <h2 class="card-head">Career Growth<br>&amp;Professional<br>Development</h2>
  <div class="card-body">
    <div class="grounds" role="img" aria-label="Company Grounds pattern in soft grey, sage and sand tones"></div>
    <ul class="card-list">
      <li>Ongoing internal training and development opportunities</li>
      <li>External study support &amp; study leave</li>
      <li>Access to the tools and technology to do your job well</li>
      <li>Career advancement opportunities</li>
      <li>Internal job vacancy listing</li>
    </ul>
  </div>
</section>

<section class="card" style="left:879px;top:310px;width:258px;height:266px">
  <h2 class="card-head">Remuneration<br>&amp; Salary Packaging</h2>
  <div class="card-body">
    <div class="grounds" role="img" aria-label="Company Grounds pattern in soft grey, sage and sand tones"></div>
    <ul class="card-list">
      <li>Competetive salary</li>
      <li>Ability to salary package up to $15,900 and reduce your tax. Package rent, home loans, child care and much more</li>
      <li>Salary package up to $2,650 on meal entertainment and holiday accommodation</li>
    </ul>
  </div>
</section>

<!-- row 2 cards -->
<section class="card" style="left:26px;top:808px;width:257px;height:229px">
  <h2 class="card-head">Diversity &amp; Inclusion</h2>
  <div class="card-body">
    <div class="grounds" role="img" aria-label="Company Grounds pattern in soft grey, sage and sand tones"></div>
    <ul class="card-list">
      <li>An inclusive and diverse culture where different backgrounds, experiences and perspectives are valued</li>
      <li>Gender diversity. Over 50% of our workforce and our leaders are female</li>
    </ul>
  </div>
</section>

<section class="card" style="left:310px;top:805px;width:255px;height:279px">
  <h2 class="card-head">Benefits</h2>
  <div class="card-body">
    <div class="grounds" role="img" aria-label="Company Grounds pattern in soft grey, sage and sand tones"></div>
    <ul class="card-list">
      <li>Discounted vouchers for Grocora, Fieldmart, Voltbay, Cinelux, Cellarhouse, Valumart, Outpost Gear and many others via Payvault e-wallet</li>
      <li>A range of other employee discounts are also available, including access to discounted banking and finance, vehicle purchasing, leasing and hotel accomodation</li>
    </ul>
  </div>
</section>

<section class="card" style="left:593px;top:808px;width:258px;height:164px">
  <h2 class="card-head">Recognition</h2>
  <div class="card-body">
    <div class="grounds" role="img" aria-label="Company Grounds pattern in soft grey, sage and sand tones"></div>
    <ul class="card-list">
      <li>We celebrate our people for reaching service milestones</li>
      <li>Team &amp; individual recognition for high performance</li>
    </ul>
  </div>
</section>

<section class="card" style="left:879px;top:808px;width:258px;height:269px">
  <h2 class="card-head">Contributing to<br>Community</h2>
  <div class="card-body">
    <div class="grounds" role="img" aria-label="Company Grounds pattern in soft grey, sage and sand tones"></div>
    <ul class="card-list">
      <li>Team involvement in local charity and community events</li>
      <li>Participation in VELMAR's 1000 Jobs in 100 days</li>
      <li>Strong relationships and connection with Indigenous Communities in support of Indigenous Emplyment</li>
    </ul>
  </div>
</section>

</body>
</html>
```